Dunmore Roofing

Want a professional looking business card

Industry/Entity Type

Business

Contact Information for Business Card

Paul Dunmore ( Owner) paul@dunmoreroofing-example.com, www.dunmoreroofing-example.com, Adress: 4172 Township road 43 Harwick Falls,QX K9X4T2

```html
<!DOCTYPE html>
<html lang="en">
<head>
<meta charset="utf-8">
<title>Dunmore Roofing – Business Card</title>
<link rel="stylesheet" href="https://fonts.googleapis.com/css2?family=Source+Sans+3:ital,wght@0,400;0,600;0,700;1,700&display=swap">
<style>
  :root {
    --page-bg: #e9e7e3;
    --card-white: #ffffff;
    --brand-blue: #1b4587;
    --brand-blue-dark: #143668;
    --strip-grey: #7d8088;
    --strip-grey-dark: #6b6e76;
    --strip-grey-light: #8d9098;
    --back-grey: #7b7c80;
    --text-white: #ffffff;
    --text-soft: #dfe6f2;
    --shadow: rgba(0, 0, 0, 0.18);
  }
  * { box-sizing: border-box; margin: 0; padding: 0; }
  html, body {
    width: 1200px;
    height: 935px;
    overflow: hidden;
  }
  body {
    background: var(--page-bg);
    font-family: "Source Sans 3", "Myriad Pro", Arial, sans-serif;
    position: relative;
  }
  .card {
    position: absolute;
    top: 318px;
    width: 525px;
    height: 300px;
    overflow: hidden;
    box-shadow: 0 6px 18px var(--shadow);
  }

  /* ---------- Front ---------- */
  .card--front {
    left: 50px;
    background: var(--card-white);
    display: flex;
  }
  .front__brand {
    width: 190px;
    flex: none;
    display: flex;
    align-items: center;
    justify-content: center;
  }
  .brand-name {
    color: var(--brand-blue);
    font-weight: 700;
    text-transform: uppercase;
    text-align: center;
    line-height: 1.1;
  }
  .brand-name__main {
    display: block;
    font-size: 28px;
    letter-spacing: 1px;
  }
  .brand-name__sub {
    display: block;
    font-size: 13px;
    letter-spacing: 10px;
    margin-top: 4px;
    padding-left: 10px;
  }
  .front__strip {
    position: relative;
    width: 40px;
    flex: none;
    background: repeating-linear-gradient(
      to bottom,
      var(--strip-grey) 0 34px,
      var(--strip-grey-dark) 34px 62px,
      var(--strip-grey-light) 62px 92px
    );
    border-left: 3px solid var(--brand-blue);
  }
  .contact-icons {
    position: absolute;
    top: 26px;
    left: 50%;
    transform: translateX(-50%);
    width: 26px;
    padding: 6px 0;
    border-radius: 13px;
    background: var(--brand-blue-dark);
    display: flex;
    flex-direction: column;
    align-items: center;
    gap: 5px;
  }
  .contact-icons svg {
    width: 16px;
    height: 16px;
    display: block;
  }
  .front__details {
    flex: 1;
    min-width: 0;
    background: var(--brand-blue);
    color: var(--text-white);
    padding: 26px 18px 24px 22px;
    font-size: 14px;
    line-height: 1.38;
    white-space: nowrap;
  }
  .person__name {
    font-weight: 700;
    font-style: italic;
    font-size: 16px;
  }
  .person__role {
    color: var(--text-soft);
    margin-bottom: 8px;
  }
  .address { margin-top: 10px; }

  /* ---------- Back ---------- */
  .card--back {
    left: 625px;
    background: var(--back-grey);
    display: flex;
    flex-direction: column;
    align-items: center;
    justify-content: center;
    gap: 20px;
  }
  .card--back .brand-name { color: var(--text-white); }
  .card--back .brand-name__main { font-size: 40px; letter-spacing: 2px; }
  .card--back .brand-name__sub { font-size: 18px; letter-spacing: 15px; padding-left: 15px; }
  .back__web {
    color: var(--text-white);
    font-size: 14px;
    letter-spacing: 0.5px;
  }
</style>
</head>
<body>
  <section class="card card--front" aria-label="Business card front">
    <div class="front__brand">
      <div class="brand-name">
        <span class="brand-name__main">Dunmore</span>
        <span class="brand-name__sub">Roofing</span>
      </div>
    </div>
    <div class="front__strip">
      <div class="contact-icons">
        <svg viewBox="0 0 16 16" aria-label="Phone">
          <rect x="0" y="0" width="16" height="16" rx="3" fill="#ffffff"/>
          <path d="M5 3.5l1.6 2.3-1 1c.6 1.3 1.4 2.1 2.7 2.7l1-1 2.2 1.6-.8 1.6c-3.6-.3-6.3-3-6.6-6.6z" fill="#143668"/>
        </svg>
        <svg viewBox="0 0 16 16" aria-label="Email">
          <rect x="0" y="0" width="16" height="16" rx="3" fill="#ffffff"/>
          <rect x="3" y="4.5" width="10" height="7" fill="none" stroke="#143668" stroke-width="1.3"/>
          <path d="M3 4.5l5 4 5-4" fill="none" stroke="#143668" stroke-width="1.3"/>
        </svg>
        <svg viewBox="0 0 16 16" aria-label="Location">
          <rect x="0" y="0" width="16" height="16" rx="3" fill="#ffffff"/>
          <path d="M8 2.8a3.4 3.4 0 0 0-3.4 3.4C4.6 9 8 13.2 8 13.2s3.4-4.2 3.4-7A3.4 3.4 0 0 0 8 2.8z" fill="#143668"/>
          <circle cx="8" cy="6.2" r="1.3" fill="#ffffff"/>
        </svg>
      </div>
    </div>
    <div class="front__details">
      <p class="person__name">Paul Dunmore</p>
      <p class="person__role">Owner</p>
      <p class="contact__phone">(555) 318-4462</p>
      <p class="contact__email">paul@dunmoreroofing-example.com</p>
      <p class="contact__web">www.dunmoreroofing-example.com</p>
      <p class="address">4172 Township road 43,<br>Harwick Falls,QX K9X4T2</p>
    </div>
  </section>

  <section class="card card--back" aria-label="Business card back">
    <div class="brand-name">
      <span class="brand-name__main">Dunmore</span>
      <span class="brand-name__sub">Roofing</span>
    </div>
    <p class="back__web">www.dunmoreroofing-example.com</p>
  </section>
</body>
</html>
```